Realtor branding business card

modern, simple and self branding. Broker office logo needs to be used but not emphasized. Looking to brand myself

Target Market(s)

buyers, sellers and investors

Industry/Entity Type

Realtor

Contact Information for Business Card

Sample of my current business card on file

Requirements
Must have
• my website - tobiasmerrowkl.com
• Realtor logo
• Fair housing logo
Nice to have
• Colors from office logo but not a must
Should not have
• Do not want headshot

```html
<!DOCTYPE html>
<html lang="en">
<head>
<meta charset="utf-8">
<title>Tobias Merrow – Realtor Business Card</title>
<link href="https://fonts.googleapis.com/css2?family=Montserrat:wght@400;500;700;800&display=swap" rel="stylesheet">
<style>
  :root {
    --card-navy: #2a2470;
    --card-navy-deep: #221d5f;
    --accent-red: #e0262c;
    --text-white: #ffffff;
    --stage-bg: #e9e9ec;
  }
  * { box-sizing: border-box; margin: 0; padding: 0; }
  html, body { width: 1200px; height: 780px; overflow: hidden; }
  body {
    background: var(--stage-bg);
    font-family: 'Montserrat', sans-serif;
    display: flex;
    flex-direction: column;
    align-items: center;
    justify-content: center;
    gap: 28px;
  }
  .card {
    width: 620px;
    height: 354px;
    background: var(--card-navy);
    position: relative;
    color: var(--text-white);
  }
  /* Front: brokerage name, pressed tone-on-tone */
  .card-front { display: flex; align-items: center; justify-content: center; }
  .front-brand {
    display: flex; align-items: center; gap: 12px;
    color: var(--card-navy-deep);
    font-weight: 800; font-size: 34px; letter-spacing: 0.5px;
  }
  .front-brand .brand-square { width: 22px; height: 22px; background: var(--card-navy-deep); }

  /* Back: brokerage name + agent details */
  .card-back { display: flex; align-items: center; }
  .back-brand {
    width: 330px; padding-left: 40px;
    display: flex; align-items: center; gap: 10px;
    font-weight: 800; font-size: 23px; color: var(--text-white);
    line-height: 1.15;
  }
  .back-brand .brand-square { flex: none; width: 16px; height: 16px; background: var(--accent-red); }
  .divider { width: 2px; height: 162px; background: var(--accent-red); margin-right: 24px; }
  .agent { font-size: 13px; }
  .agent-name { color: var(--accent-red); font-weight: 700; font-size: 17px; letter-spacing: 0.5px; }
  .agent-title { font-size: 13px; margin: 2px 0 8px; }
  .contact-list { list-style: none; }
  .contact-list li { display: flex; align-items: center; gap: 8px; line-height: 18px; }
  .contact-list svg { width: 10px; height: 10px; flex: none; }
  .contact-list .web-name { color: var(--accent-red); }
  .address { margin-top: 10px; font-size: 14px; line-height: 18px; }
</style>
</head>
<body>
  <section class="card card-front" aria-label="Card front">
    <div class="front-brand"><span class="brand-square"></span>Brightfield Realty Group</div>
  </section>

  <section class="card card-back" aria-label="Card back">
    <div class="back-brand"><span class="brand-square"></span>Brightfield<br>Realty Group</div>
    <div class="divider"></div>
    <div class="agent">
      <p class="agent-name">TOBIAS MERROW</p>
      <p class="agent-title">Realtor</p>
      <ul class="contact-list">
        <li><svg viewBox="0 0 10 10"><rect x="2.5" y="0.5" width="5" height="9" rx="1" fill="none" stroke="#e0262c"/></svg>407. 555. 0142</li>
        <li><svg viewBox="0 0 10 10"><path d="M2 1l2 2-1 1.5a6 6 0 0 0 2.5 2.5L7 6l2 2-1.5 1.5C4 9 1 6 .5 2.5z" fill="#e0262c"/></svg>407. 555. 0190</li>
        <li><svg viewBox="0 0 10 10"><rect x="0.5" y="2" width="9" height="6" fill="none" stroke="#e0262c"/><path d="M.5 2l4.5 3.5L9.5 2" fill="none" stroke="#e0262c"/></svg>info@tobiasmerrowkl.com</li>
        <li><svg viewBox="0 0 10 10"><circle cx="5" cy="5" r="4.5" fill="#e0262c"/><path d="M.5 5h9M5 .5c-2 2.5-2 6.5 0 9M5 .5c2 2.5 2 6.5 0 9" fill="none" stroke="#2a2470" stroke-width=".7"/></svg>www.<span class="web-name">tobiasmerrowkl</span>.com</li>
      </ul>
      <p class="address">480 Cedar Hollow Road<br>Lakemont Springs, FL 32799</p>
    </div>
  </section>
</body>
</html>
```